Coastline Premier Retreats Business Card Design

Design a business card for Coastline Premier Retreats. Look at the website for colors and reference. Card should have logo, name, title, office number, mobile number, email, URL and a tagline like, "Luxury Hotel & Resort Email Marketing" (This might change).

https://www.coastlinepremierretreats.example

The rest I will leave up to your imagination.

Contact Information for Business Card

Logo, name, title, office number, mobile number, email, URL and a tagline like, "Luxury Hotel & Resort Email Marketing" (This might change).

```html
<!DOCTYPE html>
<html lang="en">
<head>
<meta charset="utf-8">
<title>Coastline Premier Retreats – Business Card</title>
<link href="https://fonts.googleapis.com/css2?family=Open+Sans:wght@400;600;700&display=swap" rel="stylesheet">
<style>
  :root {
    --page: #ebe6de;
    --card-top: #e3d6c3;
    --card-bottom: #d3bfa3;
    --ink: #1c1a18;
    --ink-soft: #2b2926;
    --orange: #c9561b;
    --orange-light: #d9692a;
    --orange-deep: #a8420f;
    --tagline: #f0c7a6;
  }
  * { margin: 0; padding: 0; box-sizing: border-box; }
  html, body {
    width: 1200px; height: 1046px; overflow: hidden;
    background: var(--page);
    font-family: "Open Sans", Arial, sans-serif;
  }
  .card {
    position: absolute; left: 50px; top: 223px;
    width: 1100px; height: 600px;
    background: linear-gradient(180deg, var(--card-top), var(--card-bottom));
    border: 1px solid #cdbb9f;
    overflow: hidden;
    box-shadow: 0 10px 30px rgba(60, 40, 20, 0.18);
  }
  .brand-name {
    position: absolute; left: 0; right: 0; top: 58px;
    text-align: center;
    font-size: 44px; font-weight: 700; letter-spacing: 1px;
    color: var(--ink);
  }
  .person {
    position: absolute; right: 630px; top: 280px;
    text-align: right; white-space: nowrap;
  }
  .person-name {
    font-size: 48px; font-weight: 700; line-height: 1.1;
    color: var(--ink);
  }
  .person-name .first { color: var(--orange); }
  .person-title {
    margin-top: 10px;
    font-size: 28px; font-weight: 600;
    color: var(--ink-soft);
  }
  .divider {
    position: absolute; left: 500px; top: 268px;
    width: 3px; height: 155px; background: var(--ink);
  }
  .contacts {
    position: absolute; left: 532px; top: 276px;
    list-style: none;
  }
  .contacts li {
    display: flex; align-items: center;
    height: 35.5px; white-space: nowrap;
    font-size: 23px; color: var(--ink);
  }
  .contacts svg { width: 21px; height: 21px; margin-right: 16px; flex: none; fill: var(--orange); }
  .band { position: absolute; left: 0; top: 0; width: 1100px; height: 600px; }
  .tagline {
    position: absolute; left: 0; right: 0; top: 536px;
    text-align: center;
    font-size: 26px; color: var(--tagline);
  }
</style>
</head>
<body>
  <div class="card">
    <svg class="band" viewBox="0 0 1100 600" aria-hidden="true">
      <defs>
        <linearGradient id="bandFill" x1="0" x2="1" y1="0" y2="0">
          <stop offset="0" stop-color="var(--orange-deep)"/>
          <stop offset="0.35" stop-color="var(--orange-light)"/>
          <stop offset="0.7" stop-color="var(--orange-deep)"/>
          <stop offset="1" stop-color="var(--orange-light)"/>
        </linearGradient>
      </defs>
      <path d="M0 425 Q550 612 1100 425 L1100 600 L0 600 Z" fill="url(#bandFill)"/>
      <path d="M35 423 Q550 592 1062 423 Q550 574 35 423 Z" fill="var(--ink)"/>
    </svg>

    <div class="brand-name">Coastline Premier Retreats</div>

    <div class="person">
      <div class="person-name"><span class="first">Lena</span> Marquez</div>
      <div class="person-title">Managing Director</div>
    </div>

    <div class="divider"></div>

    <ul class="contacts">
      <li>
        <svg viewBox="0 0 24 24"><path d="M6.6 10.8a15.2 15.2 0 0 0 6.6 6.6l2.2-2.2a1 1 0 0 1 1-.25 11.4 11.4 0 0 0 3.6.57 1 1 0 0 1 1 1V20a1 1 0 0 1-1 1A17 17 0 0 1 3 4a1 1 0 0 1 1-1h3.5a1 1 0 0 1 1 1c0 1.250.2 2.45.57 3.57a1 1 0 0 1-.25 1z"/></svg>
        (555) 014-2758
      </li>
      <li>
        <svg viewBox="0 0 24 24"><path d="M7 1h10a2 2 0 0 1 2 2v18a2 2 0 0 1-2 2H7a2 2 0 0 1-2-2V3a2 2 0 0 1 2-2zm0 3v15h10V4zm4 16.2h2v1.4h-2z"/></svg>
        (555) 016-7777
      </li>
      <li>
        <svg viewBox="0 0 24 24"><path d="M12 2a10 10 0 1 0 0 20 10 10 0 0 0 0-20zm-1 17.9A8 8 0 0 1 4 12l1-.9 3 3v1a2 2 0 0 0 2 2zm6.9-2.5A2 2 0 0 0 16 16h-1v-3a1 1 0 0 0-1-1H8v-2h2a1 1 0 0 0 1-1V7h2a2 2 0 0 0 2-2v-.4a8 8 0 0 1 2.9 12.8z"/></svg>
        www.coastlinepremierretreats.example
      </li>
      <li>
        <svg viewBox="0 0 24 24"><path d="M2 9l10-7 10 7v12a1 1 0 0 1-1 1H3a1 1 0 0 1-1-1zm2 2.2V20h16v-8.8l-8 5.3z"/><circle cx="12" cy="10" r="3"/></svg>
        info@coastlinepremierretreats.example
      </li>
    </ul>

    <div class="tagline">Luxury Hotel &amp; Resort Email Marketing</div>
  </div>
</body>
</html>
```